Hip / Cool Business Card for Custom Accessory Company

I would like to get a 2 sided design for standard size business cards, glossy (2 inches x 3.5 inches). Can be landscape or portrait layout! The design should include our logo (attached). The card should be extremely clear that the company is Tidy Pebble. Should also have our URL clear. Should also use the color scheme seen on our upcoming site, tidypebble.example. The font we use is called "hurry up." Other than that, please go-to-town. We are targeting 15-45 y.o. market, with a skew on the 20-30 crowd. We do custom and stock iPhone cases as well as Cufflinks, Winestoppers; see the website for more.
Updates

Project Deadline Extended
Reason: Extending in case the US July 4th Holiday is keeping people from working!!

Industry/Entity Type

Landscape

Requirements
Must have
• Must be clear that the website is tidypebble.example. Must be clear that custom designs are an option.
Nice to have
• images of our designs. examples of our designs.
Should not have
• hard on the eyes contrasting colors such as orange on black. green on blue. Should not have any fonts that are considered "old" like Times New Roman. But decorative fonts are fine.

```html
<!DOCTYPE html>
<html lang="en">
<head>
<meta charset="utf-8">
<title>Tidy Pebble — Business Card</title>
<link href="https://fonts.googleapis.com/css2?family=Michroma&display=swap" rel="stylesheet">
<style>
  :root {
    --backdrop: #e9e9e9;
    --card: #f7f7f7;
    --card-shade: #e4e4e4;
    --ink: #111111;
    --teal: #1ea2ad;
    --grey-text: #3a3a3a;
    --white: #ffffff;
  }
  * { margin: 0; padding: 0; box-sizing: border-box; }
  html, body { width: 1200px; height: 769px; overflow: hidden; }
  body {
    background: var(--backdrop);
    font-family: "Michroma", "Arial", sans-serif;
    display: flex;
    align-items: center;
    justify-content: center;
    gap: 40px;
  }
  .card {
    position: relative;
    width: 550px;
    height: 314px;
    border-radius: 16px;
    overflow: hidden;
    background: radial-gradient(ellipse at 55% 40%, var(--white) 0%, var(--card) 55%, var(--card-shade) 100%);
    box-shadow: 0 6px 18px rgba(0,0,0,0.18);
  }
  .card-art { position: absolute; inset: 0; }
  .brand {
    position: absolute;
    display: flex;
    align-items: center;
    gap: 12px;
    color: var(--ink);
    font-size: 26px;
    font-weight: 400;
    letter-spacing: 1px;
    white-space: nowrap;
  }
  .brand-dot {
    width: 30px; height: 30px;
    border-radius: 50%;
    background: var(--teal);
    flex: none;
  }
  .back-lockup {
    position: absolute;
    left: 50%;
    top: 50%;
    transform: translate(-50%, -50%);
    display: flex;
    flex-direction: column;
    align-items: center;
    gap: 14px;
  }
  .back-lockup .brand { position: static; }
  .offer {
    color: var(--teal);
    font-size: 11px;
    letter-spacing: 1.5px;
    text-transform: uppercase;
    white-space: nowrap;
  }
  .card-front .brand { right: 34px; top: 118px; font-size: 22px; }
  .contact-list {
    position: absolute;
    left: 18px;
    top: 118px;
    list-style: none;
    color: var(--white);
    font-size: 8.5px;
    line-height: 1.55;
  }
  .contact-list li { display: flex; align-items: flex-start; gap: 6px; }
  .contact-list svg { flex: none; margin-top: 1px; }
  .holder {
    position: absolute;
    right: 22px;
    bottom: 20px;
    text-align: right;
  }
  .holder-name { color: var(--teal); font-size: 15px; letter-spacing: 0.5px; }
  .holder-role { color: var(--grey-text); font-size: 12px; letter-spacing: 0.5px; }
</style>
</head>
<body>

  <section class="card card-back" aria-label="Card back">
    <div class="back-lockup">
      <div class="brand"><span class="brand-dot"></span>Tidy Pebble</div>
      <p class="offer">Custom &amp; stock designs</p>
    </div>
  </section>

  <section class="card card-front" aria-label="Card front">
    <svg class="card-art" viewBox="0 0 550 314" width="550" height="314" aria-hidden="true">
      <path d="M0 0 L70 0 C170 110 250 240 390 314 L0 314 Z" fill="var(--ink)"/>
      <path d="M70 0 L84 0 C182 108 262 236 412 314 L390 314 C250 240 170 110 70 0 Z" fill="var(--teal)"/>
    </svg>

    <ul class="contact-list">
      <li>
        <svg width="9" height="9" viewBox="0 0 10 10"><circle cx="5" cy="5" r="5" fill="#fff"/><path d="M2.5 5.5 L5 3 L7.5 5.5 V7.5 H2.5 Z" fill="#111"/></svg>
        <span>Unit 14, Birch Yard,<br>NY 10482</span>
      </li>
      <li>
        <svg width="9" height="9" viewBox="0 0 10 10"><circle cx="5" cy="5" r="5" fill="#fff"/><rect x="3.5" y="2.5" width="3" height="5" rx="0.6" fill="#111"/></svg>
        <span>555-210-4417</span>
      </li>
      <li>
        <svg width="9" height="9" viewBox="0 0 10 10"><circle cx="5" cy="5" r="5" fill="#fff"/><rect x="3.5" y="2.5" width="3" height="5" rx="0.6" fill="#111"/></svg>
        <span>555-638-2290</span>
      </li>
      <li>
        <svg width="9" height="9" viewBox="0 0 10 10"><circle cx="5" cy="5" r="5" fill="#fff"/><rect x="2.5" y="4" width="5" height="3.5" fill="#111"/></svg>
        <span>555-904-7153</span>
      </li>
      <li>
        <svg width="9" height="9" viewBox="0 0 10 10"><circle cx="5" cy="5" r="5" fill="#fff"/><rect x="2.3" y="3.2" width="5.4" height="3.6" fill="#111"/></svg>
        <span>hello@tidypebble.example</span>
      </li>
      <li>
        <svg width="9" height="9" viewBox="0 0 10 10"><circle cx="5" cy="5" r="5" fill="#fff"/><circle cx="5" cy="5" r="2.6" fill="none" stroke="#111" stroke-width="0.9"/></svg>
        <span>www.tidypebble.example</span>
      </li>
    </ul>

    <div class="brand"><span class="brand-dot"></span>Tidy Pebble</div>

    <div class="holder">
      <p class="holder-name">JORDAN REYES</p>
      <p class="holder-role">PRESIDENT</p>
    </div>
  </section>

</body>
</html>
```